A start up Private Wine Label for export to Asia.

We are looking for the best graphic design for our very first wine label Corvessa Wines and would like the following requirements:

1. Black background - explore and play around the shade of black
2. Gold Shimmery Colour Font
3. Font should be a cursive classic posh that says Corvessa Wines
4. We would like the front graphic design to be simple and elegant and has a traditional classic feel to it.

Target Market(s)

Small scale to test the upper class market for export to Asia

Font styles to use
Script

Colors

Designer to choose colors to be used in the design.

Requirements
Must have
• Gold font for the label Corvessa Wines with shimmery touch to it.
• Elegant black background.
• Simple but elegant design.
• Attractive to the upper class market in Asia.
Nice to have
• Explore and play around with your imagination.

```html
<!DOCTYPE html>
<html lang="en">
<head>
<meta charset="UTF-8">
<title>Corvessa Wines – Label</title>
<link href="https://fonts.googleapis.com/css2?family=Pinyon+Script&display=swap" rel="stylesheet">
<style>
  :root {
    --canvas: #ffffff;
    --label-center: #161616;
    --label-edge: #000000;
    --gold: #d2a84e;
    --gold-light: #f0d27a;
    --gold-deep: #8a6128;
  }
  * { margin: 0; padding: 0; box-sizing: border-box; }
  html, body {
    width: 1200px;
    height: 1200px;
    overflow: hidden;
    background: var(--canvas);
  }
  .canvas {
    position: relative;
    width: 1200px;
    height: 1200px;
  }
  .label {
    position: absolute;
    left: 231px;
    top: 240px;
    width: 728px;
    height: 718px;
    overflow: hidden;
    background: radial-gradient(circle at 50% 52%, var(--label-center) 0%, #0b0b0b 45%, var(--label-edge) 100%);
  }
  .ornament {
    position: absolute;
    left: 105px;
    width: 528px;
    height: 160px;
  }
  .ornament--top {
    top: 0;
    background: radial-gradient(ellipse 55% 100% at 50% 0%, rgba(210,168,78,0.55) 0%, rgba(138,97,40,0.3) 55%, rgba(0,0,0,0) 100%);
  }
  .ornament--bottom {
    bottom: 0;
    background: radial-gradient(ellipse 55% 100% at 50% 100%, rgba(210,168,78,0.55) 0%, rgba(138,97,40,0.3) 55%, rgba(0,0,0,0) 100%);
  }
  .brand-name {
    position: absolute;
    left: 0;
    right: 0;
    top: 300px;
    text-align: center;
    font-family: "Pinyon Script", cursive;
    font-size: 92px;
    font-weight: 400;
    line-height: 1;
    color: var(--gold);
    white-space: nowrap;
  }
</style>
</head>
<body>
  <main class="canvas">
    <section class="label">
      <div class="ornament ornament--top" role="img" aria-label="Gold lace mandala ornament hanging from the top edge"></div>
      <h1 class="brand-name">Corvessa Wines</h1>
      <div class="ornament ornament--bottom" role="img" aria-label="Gold lace mandala ornament rising from the bottom edge"></div>
    </section>
  </main>
</body>
</html>
```